Billboard design 8x3M RAVU (Spanish company)

We´re located in the south of Spain. We run a local telecom company.
We sell Fiber optic, and mobile phone lines mainly.
The billboard will have to be in Spanish, I would like the price to be something you spot on first sight when passing by in the car.
Our company color is blue, like in our logo which I will add. I will also add a example from what we currently have.
The new offer should be:
1000 megas + 100Gigas movil con llamadas ilimitadas. (meaning 1000Mb fiber optic speed and 100Gb data and unlimited calls for 1 mobile line)
Our details are: phone line 958 47 6620
Website: ra-vu.es

```html
<!DOCTYPE html>
<html lang="es">
<head>
<meta charset="UTF-8">
<title>RAVU – Valla 8x3</title>
<link rel="stylesheet" href="https://fonts.googleapis.com/css2?family=Exo+2:wght@600;700;800&display=swap">
<style>
  :root {
    --navy: #0c4a7c;
    --cyan: #17b4ea;
    --yellow: #fdd45b;
    --white: #ffffff;
    --backdrop: #e8edf2;
    --wall-teal: #bfe3e1;
  }
  * { margin: 0; padding: 0; box-sizing: border-box; }
  html, body {
    width: 1200px; height: 874px; overflow: hidden;
    background: var(--backdrop);
    font-family: "Exo 2", sans-serif;
  }
  .billboard {
    position: absolute; left: 0; top: 219px;
    width: 1200px; height: 435px;
    background: var(--white);
    overflow: hidden;
  }
  .photo-left {
    position: absolute; left: 640px; top: 0; width: 320px; height: 400px;
    background: linear-gradient(90deg, rgba(191,227,225,0) 0%, var(--wall-teal) 45%, #a9d9dc 100%);
  }
  .photo-right {
    position: absolute; left: 957px; top: 0; width: 243px; height: 400px;
    background: linear-gradient(180deg, #f7cf4a 0%, #f1c23e 100%);
  }
  .price-badge {
    position: absolute; left: 0; top: 0; width: 600px; height: 240px;
  }
  .price {
    position: absolute; left: 290px; top: 30px; transform: translateX(-50%);
    font-size: 92px; font-weight: 800; color: var(--navy);
    letter-spacing: -2px; line-height: 1;
  }
  .price-note {
    position: absolute; left: 290px; top: 124px; transform: translateX(-50%);
    font-size: 25px; font-weight: 700; color: var(--navy); white-space: nowrap;
  }
  .brand {
    position: absolute; left: 519px; top: 18px;
    font-size: 60px; font-weight: 800; color: var(--cyan);
    line-height: 1; letter-spacing: 2px;
  }
  .services {
    position: absolute; left: 519px; top: 90px;
    font-size: 19px; font-weight: 700; color: var(--cyan); white-space: nowrap;
  }
  .offer {
    position: absolute; left: 40px; top: 220px; white-space: nowrap;
  }
  .offer-main {
    font-size: 54px; font-weight: 700; color: var(--navy); line-height: 1;
  }
  .offer-sub {
    margin-top: 4px;
    font-size: 38.5px; font-weight: 700; color: var(--cyan); line-height: 1;
  }
  .band { position: absolute; left: 0; top: 0; }
  .contact {
    position: absolute; left: 30px; top: 354px;
    display: flex; align-items: center; gap: 10px;
    color: var(--white); font-weight: 600; white-space: nowrap;
  }
  .contact-icon { width: 44px; height: 44px; flex: none; }
  .contact-phone { font-size: 52px; line-height: 1; margin-right: 6px; }
  .contact-web { font-size: 46px; line-height: 1; }
</style>
</head>
<body>
  <section class="billboard">
    <div class="photo-left" role="img" aria-label="Foto: joven con jersey amarillo mirando el móvil apoyada en una pared turquesa"></div>
    <div class="photo-right" role="img" aria-label="Foto: joven con camiseta rosa mirando el móvil frente a una pared amarilla"></div>

    <svg class="price-badge" viewBox="0 0 600 240" aria-hidden="true">
      <circle cx="290" cy="36" r="174" fill="none" stroke="#17b4ea" stroke-width="2.5" stroke-dasharray="7 6"/>
      <circle cx="290" cy="36" r="160" fill="#fdd45b"/>
    </svg>
    <div class="price">35€</div>
    <div class="price-note">Por sólo</div>

    <div class="brand">RAVU</div>
    <div class="services">Wifi | Fibra | Movil | Tv</div>

    <div class="offer">
      <div class="offer-main">1000 MEGAS + 100GIGAS</div>
      <div class="offer-sub">MOVIL CON LLAMADAS ILIMITADAS</div>
    </div>

    <svg class="band" width="1200" height="435" viewBox="0 0 1200 435" aria-hidden="true">
      <path d="M0,339 L770,333 C835,330 845,392 905,392 L1200,388 L1200,435 L0,435 Z" fill="#fdd45b"/>
      <path d="M0,346 L760,339 C830,336 840,399 905,399 L1200,395 L1200,435 L0,435 Z" fill="#0c4a7c"/>
    </svg>

    <div class="contact">
      <svg class="contact-icon" viewBox="0 0 44 44" aria-hidden="true">
        <circle cx="22" cy="22" r="21" fill="#17b4ea"/>
        <path d="M15 12c1-1 2.5-1 3.3 0l2.4 3.2c.7 1 .5 2.2-.3 3l-1.5 1.4c1 2.3 2.8 4.2 5.1 5.3l1.5-1.5c.8-.8 2.1-.9 3-.2l3.1 2.4c1 .8 1 2.3.1 3.2l-1.7 1.8c-1.3 1.3-3.3 1.6-5 .9-5.4-2.3-9.6-6.5-11.9-11.9-.7-1.7-.4-3.7.9-5z" fill="#ffffff"/>
      </svg>
      <span class="contact-phone">958 47 6620</span>
      <svg class="contact-icon" viewBox="0 0 44 44" aria-hidden="true">
        <circle cx="22" cy="22" r="21" fill="#17b4ea"/>
        <rect x="13" y="14" width="18" height="12" rx="1.5" fill="none" stroke="#ffffff" stroke-width="2.2"/>
        <rect x="10" y="28" width="24" height="2.6" rx="1.2" fill="#ffffff"/>
      </svg>
      <span class="contact-web">ra-vu.es</span>
    </div>
  </section>
</body>
</html>
```